I need 2 flyers designed for my business

Both can be similar in design and will have different purposes. I need an education based flyer and I need a government based flyer. The focus of the flyer will be software on the front and services on the back.
These all need to be 8.5x 11 in dimension (they can be full bleed). I would like to be able to print these out if needed. The design needs to look good with our website > www.brelmont.com

The software details are on the website.

```html
<!DOCTYPE html>
<html lang="en">
<head>
<meta charset="utf-8">
<title>Brelmont – Record Management Flyers</title>
<link rel="stylesheet" href="https://fonts.googleapis.com/css2?family=Poppins:ital,wght@0,300;0,400;0,600;0,700;0,800;0,900;1,600;1,700&display=swap">
<style>
  :root {
    --maroon: #7a0a0c;
    --maroon-deep: #5a0608;
    --red: #8e1012;
    --red-soft: #a3191a;
    --olive: #6a5410;
    --olive-light: #8a7420;
    --gold: #8d7a2a;
    --white: #ffffff;
    --paper: #f7f7f8;
    --ink: #1d1d1d;
    --backdrop: #d9d8dc;
  }
  * { box-sizing: border-box; margin: 0; padding: 0; }
  html, body { width: 1200px; height: 800px; overflow: hidden; }
  body {
    background: var(--backdrop);
    font-family: "Poppins", sans-serif;
    position: relative;
  }
  .flyer {
    position: absolute;
    top: 50px;
    width: 541px;
    height: 700px;
    overflow: hidden;
    box-shadow: 0 10px 30px rgba(0,0,0,.18);
  }
  .flyer--front { left: 50px; background: linear-gradient(180deg, var(--white), var(--paper)); }
  .flyer--back { left: 609px; background: var(--maroon); }

  /* ---------- Front ---------- */
  .front-shapes { position: absolute; inset: 0; }
  .brand {
    position: absolute; left: 38px; top: 98px;
    display: flex; align-items: center; gap: 10px;
    color: var(--maroon); font-weight: 800; font-size: 32px; letter-spacing: -1px; line-height: 1;
  }
  .brand__mark { width: 20px; height: 20px; background: var(--maroon); }
  .hero-visual {
    position: absolute; left: 300px; top: 112px; width: 200px; height: 158px;
    background: linear-gradient(160deg, #e8ebe6 0%, #c9d4bd 45%, #8ea07e 100%);
    border: 8px solid #e3e4e6; border-radius: 6px;
  }
  .title { position: absolute; left: 40px; top: 372px; line-height: .98; }
  .title__light { display: block; color: var(--maroon); font-weight: 300; font-size: 40px; letter-spacing: -.5px; }
  .title__bold { display: block; font-weight: 800; font-size: 44px; letter-spacing: -.5px; }
  .title__bold--olive { color: var(--olive); }
  .title__bold--maroon { color: var(--maroon); }
  .intro {
    position: absolute; left: 46px; top: 574px; width: 280px;
    padding-left: 14px; border-left: 5px solid var(--red);
    font-size: 11px; font-weight: 600; line-height: 1.45; color: var(--ink);
  }
  .portrait {
    position: absolute; left: 346px; top: 592px; width: 92px; height: 92px;
    border-radius: 50%; border: 5px solid var(--white);
    background: radial-gradient(circle at 45% 40%, #c9b9a8, #b2552a 70%, #7a2a12);
    box-shadow: 0 0 0 2px var(--olive);
  }

  /* ---------- Back ---------- */
  .back-bg {
    position: absolute; inset: 0;
    background: linear-gradient(150deg, #6d0709 0%, #9a1516 45%, #6a0608 100%);
  }
  .services-head { position: absolute; left: 0; right: 0; top: 40px; text-align: center; line-height: .9; }
  .services-head__small { display: block; color: var(--gold); font-weight: 300; font-size: 40px; }
  .services-head__big { display: block; color: var(--white); font-weight: 900; font-size: 60px; letter-spacing: 1px; }

  .service {
    position: absolute; left: 0; right: 0;
    display: grid; grid-template-columns: 130px 160px 1fr;
    align-items: center;
  }
  .service--scan { top: 165px; height: 165px; background: var(--red); }
  .service--storage { top: 330px; height: 170px; background: var(--olive); }
  .service--shred { top: 500px; height: 175px; background: var(--maroon-deep); }
  .service__pill {
    position: absolute; left: 285px; right: -40px; top: 18px; bottom: 18px;
    border-radius: 70px 0 0 70px; background: rgba(0,0,0,.14);
  }
  .service--storage .service__pill { background: rgba(0,0,0,.12); }
  .service__name {
    position: relative; text-align: center; padding: 0 8px;
    color: var(--white); font-weight: 700; font-size: 12px; line-height: 1.15; text-transform: uppercase;
  }
  .service__icon {
    display: block; width: 40px; height: 40px; margin: 0 auto 8px;
    border-radius: 50%; background: var(--olive-light);
  }
  .service__desc {
    position: relative; height: 100%; display: flex; align-items: center;
    padding: 0 14px; border-left: 1px solid rgba(255,255,255,.35);
    color: var(--white); font-style: italic; font-weight: 700; font-size: 10.5px; line-height: 1.4;
  }
  .service__list {
    position: relative; height: 100%; display: flex; flex-direction: column; justify-content: center;
    padding: 0 16px; border-left: 1px solid rgba(255,255,255,.35);
    color: var(--white); font-size: 10.5px; line-height: 1.5; list-style: none;
  }
  .service__list li::before { content: "➤ "; color: var(--gold); font-size: 9px; }
  .service--storage .service__list li::before { color: var(--red-soft); }
  .service__list .service__list-title { font-weight: 700; font-style: italic; font-size: 11.5px; margin-bottom: 2px; }
  .service__list .service__list-title::before { content: none; }
</style>
</head>
<body>

  <section class="flyer flyer--front" aria-label="Record management flyer front">
    <svg class="front-shapes" width="541" height="700" viewBox="0 0 541 700" aria-hidden="true">
      <path d="M541 30 C 420 40 360 180 380 310 C 395 410 450 465 541 478 Z" fill="var(--maroon)"/>
      <path d="M420 42 C 300 150 310 420 541 470" fill="none" stroke="var(--gold)" stroke-width="2"/>
      <polygon points="40,328 230,318 260,346 40,356" fill="var(--olive)"/>
      <polygon points="180,295 225,293 225,318 180,320" fill="var(--olive)"/>
      <polygon points="205,270 240,268 240,293 205,295" fill="var(--olive)"/>
      <polygon points="228,248 250,247 250,268 228,270" fill="var(--olive)"/>
      <polygon points="245,232 258,231 258,246 245,247" fill="var(--olive)"/>
      <polygon points="40,656 340,646 340,669 40,679" fill="var(--olive)"/>
      <g fill="var(--olive)">
        <polygon points="448,632 464,632 455,660 439,660"/>
        <polygon points="472,630 488,630 479,658 463,658"/>
        <polygon points="496,628 512,628 503,656 487,656"/>
        <polygon points="520,626 536,626 527,654 511,654"/>
      </g>
      <polygon points="40,592 50,587 50,622 40,630" fill="var(--red)"/>
    </svg>

    <div class="brand"><span class="brand__mark"></span>Brelmont</div>
    <div class="hero-visual" role="img" aria-label="Desktop monitor with paper documents flying into a blue folder, office meeting room on screen"></div>

    <h1 class="title">
      <span class="title__light">RECORD</span>
      <span class="title__bold title__bold--olive">MANAGEMENT</span>
      <span class="title__bold title__bold--maroon">SERVICES &amp;</span>
      <span class="title__bold title__bold--olive">SOFTWARE</span>
    </h1>
    <p class="intro">Brelmont Records Group offers cost-effective software and services for organizing your files and going paperless.</p>
    <div class="portrait" role="img" aria-label="Photo of a smiling woman in an orange sweater holding documents"></div>
  </section>

  <section class="flyer flyer--back" aria-label="Our services flyer back">
    <div class="back-bg" role="img" aria-label="Red background photo of stacked file folders"></div>

    <h2 class="services-head">
      <span class="services-head__small">OUR</span>
      <span class="services-head__big">SERVICES</span>
    </h2>

    <article class="service service--scan">
      <span class="service__pill"></span>
      <h3 class="service__name"><span class="service__icon"></span>Document Scanning Services</h3>
      <p class="service__desc">Fast, efficient process for the conversion of existing paper records to digital archives, increasing access and reducing onsite storage and costs.</p>
      <ul class="service__list">
        <li class="service__list-title">Scanning services for any format:</li>
        <li>Standard Office Documents</li>
        <li>16mm, 35mm Roll Microfilm</li>
        <li>Microfiche (Jackets or COM)</li>
        <li>Large Format Documents/ Drawings</li>
      </ul>
    </article>

    <article class="service service--storage">
      <span class="service__pill"></span>
      <h3 class="service__name"><span class="service__icon"></span>Offsite Document Storage</h3>
      <p class="service__desc">Solution for offsite document storage and retrieval to effectively store, manage, and safeguard your vital business records and documents.</p>
      <ul class="service__list">
        <li class="service__list-title">A local, convenient solution:</li>
        <li>Free Up Office Space</li>
        <li>Reduce Costs</li>
        <li>Keep Records in a Fireproof, Waterproof &amp; Wind-Safe Facility</li>
      </ul>
    </article>

    <article class="service service--shred">
      <span class="service__pill"></span>
      <h3 class="service__name"><span class="service__icon"></span>Secure Document Shredding</h3>
      <p class="service__desc">Safely and cost-effectively destroy unnecessary paper-based documents. One-time or recurring, our solutions are tailored to you.</p>
      <ul class="service__list">
        <li class="service__list-title">Destroy Unnecessary Documents:</li>
        <li>Protect confidential information</li>
        <li>Reduce the cost of managing information that is no longer useful</li>
        <li>Ensure compliance with regulations for information destruction</li>
      </ul>
    </article>
  </section>

</body>
</html>
```